real esate business card with company logo and name

we need a business card design for a real esate company

The company name is Walsh & Brand Pty Ltd, and we have our logo designed and will upload. We want classic or moden feel. Black or white background. looks more textured. Should include folowinginformations
Owen Walsh and Lucy Brand
Sales Agents & Onsite Manager
p: 07 5948 2063
F: 07 5948 2174
M:0431 857 219
3/42 Marlow Crescent, FERNLEA QLD 4213

We want this business card looks professonal. Thank you in advance.

Industry/Entity Type

Real Estate Agent

Contact Information for Business Card

Owen Walsh and Lucy Brand
Onsite Manager & Sales Agents
p: 07 5948 2063
M:0431 857 219

Font styles to use
Serif

Colors
000000
fbfbfb
333333
959595

Requirements
Must have
• company logo and name, black or white back ground

```html
<!DOCTYPE html>
<html lang="en">
<head>
<meta charset="utf-8">
<title>Walsh &amp; Brand Pty Ltd — Business Card</title>
<link rel="stylesheet" href="https://fonts.googleapis.com/css2?family=Oswald:wght@300;400&family=Open+Sans:wght@400;600;700&display=swap">
<style>
  :root {
    --ink: #000000;
    --paper: #fbfbfb;
    --charcoal: #333333;
    --steel: #959595;
    --stage: #e6e6e4;
    --card-w: 540px;
    --card-h: 309px;
  }
  * { box-sizing: border-box; margin: 0; padding: 0; }
  html, body { width: 1200px; height: 900px; overflow: hidden; }
  body {
    background: var(--stage);
    display: flex;
    align-items: center;
    justify-content: center;
    gap: 40px;
    font-family: "Open Sans", Arial, sans-serif;
  }
  .card {
    position: relative;
    width: var(--card-w);
    height: var(--card-h);
    overflow: hidden;
    background:
      radial-gradient(ellipse at 40% 30%, rgba(255,255,255,0.06), transparent 60%),
      repeating-linear-gradient(45deg, rgba(255,255,255,0.012) 0 2px, transparent 2px 4px),
      var(--ink);
    box-shadow: 0 12px 28px rgba(0,0,0,0.25);
  }

  /* Front */
  .card--front {
    display: flex;
    flex-direction: column;
    align-items: center;
    justify-content: center;
    gap: 26px;
  }
  .brand-mark {
    display: flex;
    align-items: center;
    gap: 14px;
  }
  .brand-mark__square {
    width: 46px;
    height: 46px;
    background: var(--steel);
  }
  .brand-mark__name {
    font-family: "Oswald", Arial, sans-serif;
    font-weight: 400;
    font-size: 40px;
    letter-spacing: 2px;
    color: var(--steel);
  }
  .company-name {
    font-family: "Oswald", Arial, sans-serif;
    font-weight: 300;
    font-size: 21px;
    letter-spacing: 2.5px;
    color: var(--steel);
  }

  /* Back */
  .card__wave {
    position: absolute;
    inset: 0;
    width: 100%;
    height: 100%;
  }
  .agent-names {
    position: absolute;
    left: 58px;
    top: 46px;
    font-size: 16px;
    font-weight: 700;
    color: var(--steel);
  }
  .agent-role {
    position: absolute;
    left: 58px;
    top: 70px;
    font-size: 12.5px;
    color: var(--paper);
  }
  .card__brand {
    position: absolute;
    right: 40px;
    top: 36px;
    font-family: "Oswald", Arial, sans-serif;
    font-size: 22px;
    letter-spacing: 1px;
    color: var(--steel);
  }
  .contact-list {
    position: absolute;
    left: 58px;
    top: 150px;
    list-style: none;
    color: var(--paper);
    font-size: 14px;
    line-height: 21px;
  }
  .contact-list li { display: flex; align-items: center; gap: 9px; }
  .contact-list svg { width: 12px; height: 12px; fill: var(--steel); }
  .address {
    position: absolute;
    left: 58px;
    top: 212px;
    color: var(--paper);
    font-size: 14px;
    line-height: 22px;
    font-style: normal;
  }
</style>
</head>
<body>

  <section class="card card--front" aria-label="Business card front">
    <div class="brand-mark">
      <span class="brand-mark__square"></span>
      <span class="brand-mark__name">WALSH &amp; BRAND</span>
    </div>
    <p class="company-name">WALSH &amp; BRAND PTY LTD.</p>
  </section>

  <section class="card card--back" aria-label="Business card back">
    <svg class="card__wave" viewBox="0 0 540 309" preserveAspectRatio="none" aria-hidden="true">
      <path d="M0,309 L0,292 C130,292 225,252 300,205 C380,158 460,150 540,150 L540,309 Z" fill="#959595"/>
      <path d="M0,278 C130,280 230,240 305,190 C375,148 450,136 540,136 L540,142 C455,145 385,160 312,200 C232,250 138,286 0,290 Z" fill="#fbfbfb"/>
    </svg>

    <h1 class="agent-names">Owen Walsh and Lucy Brand</h1>
    <p class="agent-role">Onsite Manager &amp; Sales Agents</p>
    <p class="card__brand">WALSH &amp; BRAND</p>

    <ul class="contact-list">
      <li>
        <svg viewBox="0 0 12 12"><path d="M1,4 Q6,0 11,4 L10,6 L8,5 L8,4 Q6,3 4,4 L4,5 L2,6 Z M3,7 H9 L10,11 H2 Z"/></svg>
        07 5948 2063
      </li>
      <li>
        <svg viewBox="0 0 12 12"><path d="M3,0 H9 Q10,0 10,1 V11 Q10,12 9,12 H3 Q2,12 2,11 V1 Q2,0 3,0 Z M3.2,1.5 V9 H8.8 V1.5 Z"/></svg>
        0431 857 219
      </li>
    </ul>

    <address class="address">3/42 Marlow Crescent,<br>FERNLEA QLD 4213</address>
  </section>

</body>
</html>
```